Quillmarsh Property Solutions need a business card design

Hello guys. We would need a business card design asap please.
We are a start up property investment business based in London UK specialised in buying, selling, managing and letting properties and helping distressed property owners.
The name of our Business is Quillmarsh, the logo symbolises the four fundamental elements of the world (earth, air, fire and water) and so it stands for strength, stability, longevity.
We would like the business card to communicate professionalism and reliability. Many many thanks indeed for your work.

Details:

1.) Rosalind Updike
Property Investor
Mobile: +44(0)7700123456
Email: rosalind.quillmarsh@mailbox-example.com

2.) Dominic Updike
Property Investor
Mobile: +44(0)7700987654
Email: dominic.quillmarsh@mailbox-example.com

```html
<!DOCTYPE html>
<html lang="en">
<head>
<meta charset="utf-8">
<title>Quillmarsh Property Solutions – Business Card</title>
<link rel="stylesheet" href="https://fonts.googleapis.com/css2?family=Montserrat:wght@600;800&family=Open+Sans:wght@400;600&display=swap">
<style>
  :root {
    --bg: #e8e9ed;
    --brand-blue: #2a52a6;
    --accent-red: #c22a3a;
    --paper: #ffffff;
    --ink: #111111;
    --card-w: 700px;
    --card-h: 400px;
  }
  * { box-sizing: border-box; margin: 0; padding: 0; }
  html, body {
    width: 1200px; height: 987px; overflow: hidden;
    background: var(--bg);
  }
  .canvas {
    width: 1200px; height: 987px;
    display: flex; flex-direction: column; align-items: center; justify-content: center;
    gap: 67px;
  }
  .card {
    position: relative;
    width: var(--card-w); height: var(--card-h);
    border-radius: 28px; overflow: hidden;
    box-shadow: 0 6px 18px rgba(0,0,0,0.15);
  }
  .card--front { background: var(--paper); }
  .card--back { background: var(--brand-blue); display: flex; align-items: center; justify-content: center; }
  .card-art { position: absolute; inset: 0; }
  .wordmark { position: absolute; left: 300px; top: 110px; }
  .wordmark__name {
    display: flex; align-items: center; gap: 12px;
    font-family: "Montserrat", sans-serif; font-weight: 800;
    font-size: 40px; letter-spacing: 1px; color: var(--ink);
  }
  .wordmark__dot { width: 16px; height: 16px; background: var(--brand-blue); }
  .wordmark__tagline {
    margin-top: 4px; margin-left: 30px;
    font-family: "Montserrat", sans-serif; font-weight: 600;
    font-size: 13px; letter-spacing: 1.5px; color: var(--ink);
  }
  .contact {
    position: absolute; left: 38px; top: 302px;
    display: flex; align-items: center; gap: 18px;
    font-family: "Open Sans", sans-serif; color: var(--paper);
  }
  .contact__person { text-align: left; }
  .contact__name { font-size: 24px; font-weight: 600; white-space: nowrap; }
  .contact__role { font-size: 17px; font-weight: 400; opacity: 0.95; }
  .contact__divider { width: 2px; height: 52px; background: var(--paper); opacity: 0.8; }
  .contact__lines { display: flex; flex-direction: column; gap: 6px; font-size: 17px; white-space: nowrap; }
  .contact__line { display: flex; align-items: center; gap: 9px; }
  .contact__icon { width: 18px; height: 18px; flex: none; }
  .back-mark {
    display: flex; align-items: center; gap: 16px;
    font-family: "Montserrat", sans-serif; font-weight: 800;
    font-size: 52px; letter-spacing: 2px; color: var(--paper);
  }
  .back-mark__dot { width: 22px; height: 22px; background: var(--paper); }
</style>
</head>
<body>
<main class="canvas">
  <section class="card card--front" aria-label="Business card front">
    <svg class="card-art" viewBox="0 0 700 400" aria-hidden="true">
      <path fill="var(--accent-red)" d="M0,72 C150,212 380,252 620,260 C380,264 150,232 0,94 Z"/>
      <path fill="var(--brand-blue)" d="M0,110 C150,250 380,290 700,270 L700,400 L0,400 Z"/>
    </svg>
    <div class="wordmark">
      <div class="wordmark__name"><span class="wordmark__dot"></span>QUILLMARSH</div>
      <div class="wordmark__tagline">PROPERTY SOLUTIONS</div>
    </div>
    <div class="contact">
      <div class="contact__person">
        <div class="contact__name">Dominic Updike</div>
        <div class="contact__role">Property Investor</div>
      </div>
      <div class="contact__divider"></div>
      <div class="contact__lines">
        <div class="contact__line">
          <svg class="contact__icon" viewBox="0 0 18 18" aria-hidden="true">
            <rect x="4" y="1" width="10" height="16" rx="2" fill="none" stroke="#fff" stroke-width="1.6"/>
            <rect x="6" y="3.5" width="6" height="6" fill="#fff"/>
            <circle cx="9" cy="13.5" r="1.2" fill="#fff"/>
          </svg>
          <span>+44(0)7700987654</span>
        </div>
        <div class="contact__line">
          <svg class="contact__icon" viewBox="0 0 18 18" aria-hidden="true">
            <rect x="1.5" y="4" width="15" height="10" rx="1.5" fill="none" stroke="#fff" stroke-width="1.6"/>
            <path d="M2,5 L9,10 L16,5" fill="none" stroke="#fff" stroke-width="1.6"/>
          </svg>
          <span>dominic.quillmarsh@mailbox-example.com</span>
        </div>
      </div>
    </div>
  </section>

  <section class="card card--back" aria-label="Business card back">
    <div class="back-mark"><span class="back-mark__dot"></span>QUILLMARSH</div>
  </section>
</main>
</body>
</html>
```